Simple and Clean business card design

We would like the design to be simple clean and to incorporate our colors.

We are open to your design and talent, we have the dots in our logo as we think of it as data points and we connect data points for people.

We are open to see the great creative and clean design you bring to the table

Contact Information for Business Card

please include: name, position, email, phone and website

Font styles to use
Sans Serif

Requirements
Must have
• my colors incorporated, simplicity
Nice to have
• lots of white space, simplicity
Should not have
• complexicity/ complex art

```html
<!DOCTYPE html>
<html lang="en">
<head>
<meta charset="UTF-8">
<title>Brindle — Business Card</title>
<link rel="stylesheet" href="https://fonts.googleapis.com/css2?family=Montserrat:wght@400;500;600;700&display=swap">
<style>
  :root {
    --backdrop: #3a3a3a;
    --card: #ffffff;
    --ink: #111111;
    --green: #31a956;
    --name-green: #4cb97a;
    --blue: #577fc2;
    --rule: #9a9a9a;
  }
  * { margin: 0; padding: 0; box-sizing: border-box; }
  html, body {
    width: 1200px;
    height: 1200px;
    overflow: hidden;
    background: var(--backdrop);
    font-family: "Montserrat", sans-serif;
  }
  .canvas { position: relative; width: 1200px; height: 1200px; }
  .card {
    position: absolute;
    left: 240px;
    width: 720px;
    height: 420px;
    background: var(--card);
    border-radius: 48px;
  }
  .card--front { top: 142px; }
  .card--back { top: 638px; }

  .brand {
    position: absolute;
    display: flex;
    align-items: center;
    color: var(--ink);
    font-weight: 600;
    line-height: 1;
    white-space: nowrap;
  }
  .brand__dot { border-radius: 50%; background: var(--green); flex: none; }

  .brand--front {
    left: 104px;
    top: 188px;
    font-size: 50px;
    gap: 10px;
  }
  .brand--front .brand__dot { width: 18px; height: 18px; }

  .divider {
    position: absolute;
    left: 348px;
    top: 137px;
    width: 1.5px;
    height: 151px;
    background: var(--rule);
  }

  .details { position: absolute; left: 374px; top: 134px; }
  .details__name {
    color: var(--name-green);
    font-weight: 700;
    font-size: 30px;
    line-height: 30px;
    letter-spacing: 0.2px;
  }
  .details__role {
    color: var(--ink);
    font-size: 17px;
    line-height: 21px;
    margin-top: 1px;
  }
  .details__company {
    color: var(--name-green);
    font-size: 17px;
    line-height: 21px;
  }
  .contacts { list-style: none; margin-top: 14px; }
  .contacts__item {
    display: flex;
    align-items: center;
    gap: 8px;
    height: 23px;
    color: var(--ink);
    font-size: 17px;
    letter-spacing: 0.6px;
    white-space: nowrap;
  }
  .contacts__icon { width: 19px; height: 19px; flex: none; }

  .brand--back {
    left: 50%;
    top: 50%;
    transform: translate(-50%, -50%);
    font-size: 72px;
    gap: 16px;
  }
  .brand--back .brand__dot { width: 30px; height: 30px; background: var(--blue); }
</style>
</head>
<body>
<main class="canvas">
  <section class="card card--front" aria-label="Card front">
    <div class="brand brand--front">
      <span class="brand__name">Brindle</span>
      <span class="brand__dot"></span>
    </div>

    <div class="divider"></div>

    <div class="details">
      <h1 class="details__name">NORA VALE</h1>
      <p class="details__role">Founder/ CEO</p>
      <p class="details__company">Brindle.Works</p>
      <ul class="contacts">
        <li class="contacts__item">
          <svg class="contacts__icon" viewBox="0 0 20 20" aria-hidden="true">
            <circle cx="10" cy="10" r="10" fill="var(--blue)"/>
            <path d="M6.6 5.2c.4-.3.9-.2 1.1.2l1 1.7c.2.4.1.8-.2 1.1l-.6.5c.5 1.1 1.4 2 2.5 2.5l.5-.6c.3-.3.7-.4 1.1-.2l1.7 1c.4.2.5.7.2 1.1l-.7.9c-.4.5-1.1.6-1.7.4-2.6-1-4.6-3-5.6-5.6-.2-.6-.1-1.3.4-1.7z" fill="#fff"/>
          </svg>
          <span>555-214-0198</span>
        </li>
        <li class="contacts__item">
          <svg class="contacts__icon" viewBox="0 0 20 20" aria-hidden="true">
            <circle cx="10" cy="10" r="10" fill="var(--blue)"/>
            <rect x="5.3" y="6.8" width="9.4" height="6.6" rx="1" fill="#fff"/>
            <path d="M5.8 7.4l4.2 3.1 4.2-3.1" fill="none" stroke="var(--blue)" stroke-width="1"/>
          </svg>
          <span>nora.vale@brindle.works</span>
        </li>
        <li class="contacts__item">
          <svg class="contacts__icon" viewBox="0 0 20 20" aria-hidden="true">
            <circle cx="10" cy="10" r="10" fill="var(--blue)"/>
            <g fill="none" stroke="#fff" stroke-width="0.9">
              <circle cx="10" cy="10" r="5"/>
              <ellipse cx="10" cy="10" rx="2.2" ry="5"/>
              <line x1="5" y1="10" x2="15" y2="10"/>
              <line x1="10" y1="5" x2="10" y2="15"/>
              <line x1="5.7" y1="7.6" x2="14.3" y2="7.6"/>
              <line x1="5.7" y1="12.4" x2="14.3" y2="12.4"/>
            </g>
          </svg>
          <span>www.Brindle.works</span>
        </li>
      </ul>
    </div>
  </section>

  <section class="card card--back" aria-label="Card back">
    <div class="brand brand--back">
      <span class="brand__name">Brindle</span>
      <span class="brand__dot"></span>
    </div>
  </section>
</main>
</body>
</html>
```